Aquatic View

We need a web design for a new window cleaning company name Tidewell Glass Care. We are located in Grand Cayman, Cayman Islands. We are a small company, a team of husband and wife. Our services include residencial interior and exterior window cleaning and commercial. Extra services such as ceiling fans cleaning, mirrors, high dusting. Home cleaning services. Power washing. Explaining the service. We want a modern, beachy style with aquatic colors. We want to use our domain name "tidewellglasscare.ky". We want to portray a clean, modern and professional design.

Target Market(s)

Big Home owners

Industry/Entity Type

Cleaning Service

Contact Information for Business Card

Company Name: Tidewell Glass Care
Name: Desmond Farrowby owner/manager
Phone: 345-9170452
Email: desmond@tidewellglasscare.ky
Website: tidewellglasscare.ky
Address: P.O.Box 2486 GT, George Town, Grand Cayman KY1-1203 Cayman Islands

Number of Pages Required

2 page

Font styles to use
Sans Serif

Colors
0592cd
0455a3
33a6d7
85cae6
cadf82
abd036
fbf289

Requirements
Nice to have
• Pictures of an ocean view and palm trees from clear windows.
• https://quorvantel.com/bidlinker/
• Use the above for "free estimate".

```html
<!DOCTYPE html>
<html lang="en">
<head>
<meta charset="utf-8">
<title>Tidewell Glass Care</title>
<link href="https://fonts.googleapis.com/css2?family=Open+Sans:ital,wght@0,400;0,600;0,700;1,400&family=Raleway:wght@300;700;800&display=swap" rel="stylesheet">
<style>
:root{
  --ink:#333;
  --muted:#666;
  --blue:#0455a3;
  --blue-bright:#0592cd;
  --blue-mid:#1a6bb5;
  --green:#abd036;
  --dark:#333333;
  --darker:#2a2a2a;
  --topbar:#2b2b2b;
  --card:#f4f4f4;
}
*{box-sizing:border-box;margin:0;padding:0}
html,body{width:748px;height:1200px;overflow:hidden;background:#fff}
body{position:relative;font-family:"Open Sans",sans-serif;color:var(--ink)}
.abs{position:absolute}

.topbar{left:0;top:0;width:748px;height:23px;background:var(--topbar);color:#fff;font-size:8px}
.topbar .addr{left:62px;top:6px;display:flex;align-items:center;gap:3px}
.topbar .mail{right:70px;top:6px;display:flex;align-items:center;gap:5px}

.header{left:0;top:23px;width:748px;height:78px;background:#fff}
.brand{left:62px;top:29px;display:flex;align-items:center;gap:6px;font-family:"Raleway",sans-serif;font-weight:800;font-size:10px;color:var(--blue);line-height:1.05;text-transform:uppercase}
.brand .dot{width:16px;height:16px;border-radius:50%;background:var(--blue-bright)}
.callus{left:288px;top:26px;display:flex;align-items:center;gap:8px}
.callus small{display:block;font-size:7.5px;color:#444}
.callus strong{display:block;font-weight:400;font-size:12.5px;color:var(--blue-mid)}
.search{left:500px;top:29px;width:186px;height:24px;border:1px solid #ccc;display:flex}
.search span{flex:1;font-size:7.5px;color:#777;padding:7px 8px}
.search b{width:28px;background:var(--blue);display:flex;align-items:center;justify-content:center}

.nav{left:0;top:101px;width:748px;height:33px;background:linear-gradient(#2479c3,#0b4f96);border-bottom:2px solid var(--green)}
.nav a{position:absolute;top:0;height:31px;line-height:31px;font-size:7.5px;color:#fff;text-decoration:none;text-align:center}
.nav a.active{background:var(--green);left:62px;width:78px}
.nav .sep{position:absolute;top:0;width:1px;height:31px;background:rgba(255,255,255,.12)}

.hero{left:0;top:134px;width:748px;height:304px;background:linear-gradient(180deg,#7fb9d8 0%,#2f84b8 30%,#cfd6d6 55%,#e9e3d6 70%,#9a9a8c 100%)}
.hero h1{position:absolute;left:62px;top:116px;font-family:"Raleway",sans-serif;color:#fff;line-height:1.1}
.hero h1 .l1{display:block;font-weight:300;font-size:17px}
.hero h1 .l2{display:block;font-weight:800;font-size:23px}
.cta{left:62px;top:164px;width:120px;height:32px;background:var(--green);color:#fff;font-size:9px;font-weight:700;text-align:center;line-height:32px}
.arrow{top:120px}

.video{left:62px;top:468px;width:214px;height:144px;background:linear-gradient(135deg,#c9ced2,#8d969c 60%,#e4c23c)}
.video .play{position:absolute;left:95px;top:60px}
.welcome{left:297px;top:470px;width:360px}
.welcome h2{font-family:"Raleway",sans-serif;font-weight:700;font-size:16px;color:#333}
.welcome h2 span{color:var(--blue-bright);margin-left:6px}
.welcome p{margin-top:8px;font-size:7.4px;line-height:14.8px;color:var(--muted)}
.btn{background:var(--blue);color:#fff;font-weight:700;text-align:center;border-radius:2px}
.more-info{left:297px;top:580px;width:119px;height:32px;line-height:32px;font-size:8.5px}

.divider{left:80px;top:647px;width:576px;height:2px;background:linear-gradient(90deg,transparent,#e6e6e6,transparent)}
.services-title{left:0;top:678px;width:748px;text-align:center;font-family:"Raleway",sans-serif;font-weight:800;font-size:14.5px;color:#333}
.services-title span{color:var(--blue-mid)}

.card{top:713px;width:149px;height:253px;background:var(--card)}
.card .ph{height:127px}
.card h3{position:absolute;left:12px;top:147px;font-size:7.8px;font-weight:700;color:#222}
.card p{position:absolute;left:12px;top:164px;width:130px;font-size:7.2px;line-height:14.5px;color:var(--muted)}
.card .btn{position:absolute;left:12px;top:217px;width:79px;height:23px;line-height:23px;font-size:6.8px}

.footer{left:0;top:990px;width:748px;height:166px;background:var(--dark);color:#ccc}
.footer h4{position:absolute;top:26px;font-size:8.2px;font-weight:700;color:#fff}
.links{position:absolute;left:62px;top:50px;list-style:none;font-size:7px;color:#bbb}
.links li{height:13.4px;display:flex;align-items:center;gap:8px}
.quote{position:absolute;left:190px;top:48px;width:225px}
.quote p{padding-left:13px;font-style:italic;font-size:6.8px;line-height:14.5px;color:#aaa}
.quote .mark{position:absolute;font-family:Georgia,serif;font-size:15px;color:#777}
.quote .who{margin:3px 0 0 9px;font-size:7.2px;color:#eee}
.quote .role{margin-left:15px;font-size:6.6px;font-style:italic;color:#ccc}
.field{position:absolute;height:18px;border:1px solid #666;font-size:6.4px;color:#999;padding:4px 6px;width:111px}
.lookup{position:absolute;left:572px;top:108px;width:110px;height:18px;line-height:18px;font-size:6.5px;background:linear-gradient(#2479c3,#0b4f96)}

.chat{left:674px;top:1136px;width:74px;height:20px;background:var(--green);color:#fff;font-size:6.5px;font-weight:700;display:flex;align-items:center;justify-content:center;gap:3px;border-radius:2px 0 0 0}
.bottombar{left:0;top:1156px;width:748px;height:44px;background:var(--darker);color:#aaa;font-size:7px}
.bottombar .copy{position:absolute;left:62px;top:17px}
.bottombar .social{position:absolute;left:481px;top:15px;display:flex;align-items:center;gap:13px}
.bottombar .social i{display:block;width:8px;height:8px;border-radius:50%;background:#888}
.bottombar .code{position:absolute;left:713px;top:17px}
</style>
</head>
<body>

<div class="abs topbar">
  <div class="abs addr">
    <svg width="7" height="9" viewBox="0 0 7 9"><path d="M3.5 0A3.5 3.5 0 0 0 0 3.5C0 6 3.5 9 3.5 9S7 6 7 3.5A3.5 3.5 0 0 0 3.5 0zm0 5A1.4 1.4 0 1 1 3.5 2.2 1.4 1.4 0 0 1 3.5 5z" fill="#fff"/></svg>
    P.O.Box 2486 GT, George Town, Grand Cayman KY1-1203
  </div>
  <div class="abs mail">
    <svg width="11" height="8" viewBox="0 0 11 8"><rect width="11" height="8" rx="1" fill="#fff"/><path d="M0.5 0.8 5.5 4.6 10.5 0.8" stroke="#2b2b2b" fill="none"/></svg>
    desmond@tidewellglasscare.ky
  </div>
</div>

<header class="abs header">
  <div class="abs brand"><span class="dot"></span><span>Tidewell<br>Glass Care</span></div>
  <div class="abs callus">
    <svg width="14" height="18" viewBox="0 0 14 18"><path d="M3 1c1 0 2 3 2 4S3.5 6.5 3.5 7.5 6 12.5 7 13s1.5-1 2.5-1 3.5 2 3.5 3-1.5 2-2.5 2C6 17 1 10 1 4 1 2 2 1 3 1z" fill="#8bc34a"/></svg>
    <div><small>Call us</small><strong>+1 345 917 0452</strong></div>
  </div>
  <div class="abs search">
    <span>Search your keywords...</span>
    <b><svg width="10" height="10" viewBox="0 0 10 10"><circle cx="4" cy="4" r="3" stroke="#fff" stroke-width="1.6" fill="none"/><path d="M6.3 6.3 9 9" stroke="#fff" stroke-width="1.8"/></svg></b>
  </div>
</header>

<nav class="abs nav">
  <a class="active" href="#">Home</a>
  <a href="#" style="left:140px;width:80px">About</a><span class="sep" style="left:220px"></span>
  <a href="#" style="left:220px;width:72px">Service</a><span class="sep" style="left:292px"></span>
  <a href="#" style="left:292px;width:82px">Portfolio</a><span class="sep" style="left:374px"></span>
  <a href="#" style="left:374px;width:64px">Shop</a><span class="sep" style="left:438px"></span>
  <a href="#" style="left:438px;width:72px">Pages</a><span class="sep" style="left:510px"></span>
  <a href="#" style="left:510px;width:58px">Blog</a><span class="sep" style="left:568px"></span>
  <a href="#" style="left:568px;width:110px">Free instant quote</a>
</nav>

<section class="abs hero" role="img" aria-label="Bright living room with a sofa and round table in front of tall windows looking out over the ocean">
  <svg class="abs arrow" style="left:34px" width="12" height="42" viewBox="0 0 12 42"><path d="M11 1 1 21 11 41" stroke="#fff" stroke-width="1.2" fill="none"/></svg>
  <svg class="abs arrow" style="left:710px" width="12" height="42" viewBox="0 0 12 42"><path d="M1 1 11 21 1 41" stroke="#fff" stroke-width="1.2" fill="none"/></svg>
  <h1><span class="l1">WE ARE RESIDENTIAL</span><span class="l2">WINDOW CLEANING</span></h1>
  <div class="abs cta">CALL TO ACTION</div>
</section>

<div class="abs video" role="img" aria-label="Video still of a gloved hand cleaning a window with a sponge and spray bottle">
  <svg class="play" width="24" height="24" viewBox="0 0 24 24"><circle cx="12" cy="12" r="11" fill="rgba(0,0,0,.45)" stroke="#fff" stroke-width="1.5"/><path d="M9.5 7.5 16.5 12 9.5 16.5z" fill="#fff"/></svg>
</div>
<div class="abs welcome">
  <h2>WELCOME TO<span>TIDEWELL GLASS CARE</span></h2>
  <p>We are a husband and wife team based in George Town, Grand Cayman, caring for the glass of homes and businesses across the island. Salt spray, sun and sea breeze leave film on every pane, so we clean interior and exterior windows by hand with streak-free methods. We also take care of ceiling fans, mirrors, high dusting, home cleaning and power washing, so your ocean view stays as clear as the day it was built.</p>
</div>
<div class="abs btn more-info">VIEW MORE INFO</div>

<div class="abs divider"></div>
<h2 class="abs services-title">OUR <span>SERVICES</span></h2>

<article class="abs card" style="left:62px">
  <div class="ph" role="img" aria-label="Worker on ropes cleaning the glass facade of a tall building" style="background:linear-gradient(135deg,#e8eaec,#8a9096 60%,#3d4a55)"></div>
  <h3>EXTERIOR WINDOW CLEANING</h3>
  <p>Salt and sand washed off every pane, frame and track for homes and commercial sites...</p>
  <div class="btn">VIEW MORE</div>
</article>
<article class="abs card" style="left:220px">
  <div class="ph" role="img" aria-label="Hands wiping a ceiling fan with a yellow cloth" style="background:linear-gradient(135deg,#cfcfcf,#e8e4da 50%,#e6c96a)"></div>
  <h3>CEILING FANS CLEANING</h3>
  <p>Blades, housings and lights dusted and wiped down, with high dusting on request...</p>
  <div class="btn">VIEW MORE</div>
</article>
<article class="abs card" style="left:378px">
  <div class="ph" role="img" aria-label="Yellow gloved hand washing a soapy mirror" style="background:linear-gradient(135deg,#6b9cc9,#a9c6e0 45%,#e8d040 70%,#7aa3cc)"></div>
  <h3>MIRRORS</h3>
  <p>Bathroom, closet and wall mirrors polished clear with no streaks or water spots...</p>
  <div class="btn">VIEW MORE</div>
</article>
<article class="abs card" style="left:537px">
  <div class="ph" role="img" aria-label="Cleaner squeegeeing a large glass roof panel under blue sky" style="background:linear-gradient(180deg,#3f7fbd,#6fa6d8 55%,#9cb8c8)"></div>
  <h3>POWER WASHING</h3>
  <p>Driveways, decks, patios and pool areas cleared of mildew, sand and sea grime...</p>
  <div class="btn">VIEW MORE</div>
</article>

<footer class="abs footer">
  <h4 style="left:62px">QUICK LINKS</h4>
  <ul class="links">
    <li>› <span>Home</span></li><li>› <span>About</span></li><li>› <span>Service</span></li>
    <li>› <span>Portfolio</span></li><li>› <span>Shop</span></li><li>› <span>Pages</span></li><li>› <span>Blog</span></li>
  </ul>
  <h4 style="left:202px">HAPPY CUSTOMERS NEAR YOU</h4>
  <div class="quote">
    <span class="mark" style="left:0;top:-4px">“</span>
    <p>Our beach house windows had not looked this clear in years. Friendly, careful and right on time, we now book them every month...</p>
    <span class="mark" style="left:141px;top:34px">”</span>
    <div class="who">- MARA QUENTELL</div>
    <div class="role">Home owner</div>
  </div>
  <h4 style="left:451px">CONTACT DETAILS</h4>
  <div class="field" style="left:451px;top:51px">First Name</div>
  <div class="field" style="left:572px;top:51px;width:110px">Email address</div>
  <div class="field" style="left:451px;top:79px">Phone number</div>
  <div class="field" style="left:572px;top:79px;width:110px">House no</div>
  <div class="field" style="left:451px;top:108px">Product no</div>
  <div class="btn lookup">LOOK UP ADDRESS</div>
</footer>

<div class="abs chat">
  <svg width="10" height="8" viewBox="0 0 10 8"><ellipse cx="4" cy="3.2" rx="4" ry="3" fill="#fff"/><path d="M2 5.5 1 7.8 4 6z" fill="#fff"/></svg>
  LIVE CHAT
</div>

<div class="abs bottombar">
  <span class="copy">© Tidewell Glass Care 2015 . All rights reserved</span>
  <div class="social"><span>Connect with our social network :</span><i></i><i></i><i></i><i></i><i></i></div>
  <span class="code">C12</span>
</div>

</body>
</html>
```